Export company based in South America (Ecuador) we export flowers, chocolate, and bananas

We need a website that gives our potential clients and introduction into our company and the different types of commodities we export around the world. We are based in Quito, Ecuador so the website should portray the feel of Ecuadorian landscapes within a modern looking website.
At the moment we are exporting roses, chocolate, and bananas so the website should have an intro to our company and then three different areas that describe our three main commodity. The three different sections should explain why each of the products from Ecuador are some of the best in the world in their categories and the benefits of importing the commodity through our company.
Industry/Entity Type
Commodity
Number of Pages Required
4 page

```html
<!DOCTYPE html>
<html lang="en">
<head>
<meta charset="utf-8">
<title>Verandina – Ecuadorian Exports</title>
<link href="https://fonts.googleapis.com/css2?family=Russo+One&family=Roboto:wght@400;500;700&display=swap" rel="stylesheet">
<style>
:root{
  --green:#3aa935;
  --green-dark:#2e8f2a;
  --blue:#3a62ad;
  --blue-dark:#2c4f94;
  --yellow:#e8b325;
  --ink:#2b2b2b;
  --text:#888;
  --panel:#f7f7f7;
  --dark:#222;
  --white:#fff;
}
*{margin:0;padding:0;box-sizing:border-box}
html,body{width:1200px;height:4084px;overflow:hidden;background:var(--white);font-family:'Roboto',sans-serif;color:var(--ink)}
.page{position:relative;width:1200px;height:4084px;overflow:hidden}
.abs{position:absolute}
.heading{font-family:'Russo One',sans-serif;color:var(--ink);letter-spacing:1px}

/* header */
.topbar{left:600px;top:0;width:600px;height:38px}
.topbar-text{left:660px;top:8px;color:var(--white);font-size:15px;font-weight:500;white-space:nowrap}
.topbar-text b{font-size:19px;font-weight:700;margin-right:18px}
.brand{left:145px;top:30px;display:flex;align-items:center;gap:10px;font-size:46px;font-weight:500;color:var(--green)}
.brand-dot{width:40px;height:40px;border-radius:50%;background:var(--blue)}
.nav{left:452px;top:72px;display:flex;gap:30px;font-size:15px;font-weight:500;color:var(--ink)}
.nav .active{color:var(--green)}

/* hero */
.hero{left:0;top:120px;width:1200px;height:660px}
.hero-title{left:0;top:255px;width:1200px;text-align:center;font-family:'Russo One',sans-serif;font-size:86px;color:var(--white);letter-spacing:12px}
.hero-sub{left:0;top:372px;width:1200px;text-align:center;color:var(--white);font-size:25px;font-weight:500;line-height:32px;text-shadow:0 1px 3px rgba(0,0,0,.4)}
.dots{left:1125px;top:340px;display:flex;flex-direction:column;gap:10px}
.dots span{width:12px;height:12px;border-radius:50%;border:2px solid var(--white)}
.dots span.on{background:var(--white)}
.bubble{border-radius:50%;text-align:center;color:var(--white);border:6px solid rgba(255,255,255,.15)}
.bubble h3{font-size:20px;font-weight:500;margin-top:8px}
.bubble p{font-size:13px;line-height:22px;margin:14px auto 0;width:230px}
.bubble .more{font-size:15px;font-weight:700;margin-top:14px;display:block}
.b-flowers{left:156px;top:547px;width:300px;height:300px;background:var(--green);padding-top:30px}
.b-choc{left:435px;top:531px;width:332px;height:332px;background:var(--blue);padding-top:46px;z-index:2}
.b-banana{left:752px;top:547px;width:300px;height:300px;background:var(--yellow);padding-top:30px}

/* welcome */
.welcome-h{left:0;top:940px;width:1200px;text-align:center;font-size:40px}
.welcome-p{left:200px;top:1020px;width:800px;text-align:center;font-size:13px;line-height:30px;color:var(--text)}
.feature{width:200px;text-align:center}
.feature .ring{width:102px;height:102px;border-radius:50%;border:2px solid #ddd;margin:0 auto;display:flex;align-items:center;justify-content:center}
.feature span{display:block;margin-top:16px;font-size:15px;font-weight:500}

/* product rows */
.photo{width:600px;height:494px}
.panel{width:600px;height:494px;background:var(--panel)}
.prod-h{font-size:40px}
.prod-p{width:415px;font-size:13px;line-height:27px;color:var(--text)}
.btn{width:154px;height:48px;border-radius:24px;color:var(--white);font-size:14px;font-weight:700;display:flex;align-items:center;justify-content:center}
.notch{width:86px;height:86px;border-radius:50%;background:var(--panel)}

/* why */
.why-h{left:0;top:3015px;width:1200px;text-align:center;font-size:40px}
.why-icon{width:92px;height:92px;border-radius:50%;border:2px solid #eee;display:flex;align-items:center;justify-content:center;background:var(--white)}
.why-t{font-size:19px;font-weight:500}
.why-p{width:320px;font-size:13px;line-height:23px;color:var(--text)}

/* contact */
.contact-h{left:0;top:3655px;width:1200px;text-align:center;font-size:40px;color:var(--white)}
.label{font-size:15px;font-weight:700;color:var(--white)}
.field{background:var(--white);border:1px solid #ccc;font-size:10px;color:#666;padding:8px 10px}
.submit{left:631px;top:3936px;width:78px;height:27px;border-radius:14px;background:var(--green);color:var(--white);font-size:11px;font-weight:700;display:flex;align-items:center;justify-content:center}
.info-icon{width:34px;height:34px;border-radius:50%;border:2px solid var(--white);display:flex;align-items:center;justify-content:center}
.info-t{font-size:11px;line-height:20px;color:var(--white);width:225px}
.social{width:26px;height:26px;border-radius:50%}
.rule{left:135px;top:4007px;width:930px;height:1px;background:#444}
.copy{left:0;top:4035px;width:1200px;text-align:center;font-size:11px;color:var(--white)}
</style>
</head>
<body>
<div class="page">

  <!-- header -->
  <svg class="abs topbar" width="600" height="38" viewBox="0 0 600 38"><polygon points="0,0 600,0 600,38 38,38" fill="var(--blue)"/></svg>
  <div class="abs topbar-text"><b>&#9742; 1 555 010 2040</b>| &nbsp; &#9993; Email : info@verandina.com</div>
  <div class="abs brand"><span class="brand-dot"></span>Verandina</div>
  <nav class="abs nav"><span class="active">HOME</span><span>ABOUT US</span><span>PRODUCTS</span><span>WHY CHOOSE US</span><span>NEWS</span><span>CONTACT</span></nav>

  <!-- hero -->
  <svg class="abs hero" width="1200" height="660" viewBox="0 0 1200 660" role="img" aria-label="Greenhouse filled with pink and purple hydrangea flowers">
    <defs>
      <linearGradient id="heroGrad" x1="0" y1="0" x2="0" y2="1">
        <stop offset="0" stop-color="#6f8a4c"/>
        <stop offset=".45" stop-color="#a3557f"/>
        <stop offset="1" stop-color="#4f7a3a"/>
      </linearGradient>
    </defs>
    <rect width="1200" height="660" fill="url(#heroGrad)"/>
    <path d="M0 650 Q600 470 1200 650 L1200 660 L0 660 Z" fill="var(--white)"/>
    <path d="M0 650 Q600 470 1200 650" fill="none" stroke="var(--green)" stroke-width="3"/>
  </svg>
  <div class="abs hero-title">VERANDINA</div>
  <div class="abs hero-sub">Lorem ipsum dolor sit amet, consectetur adipiscing elit<br>sed do eiusmod tempor incididunt ut labore</div>
  <div class="abs dots"><span></span><span></span><span></span><span class="on"></span></div>

  <div class="abs bubble b-flowers">
    <svg width="56" height="70" viewBox="0 0 56 70"><path d="M28 68 V30 M28 46 Q14 40 10 28 M28 50 Q42 42 46 32" stroke="#fff" stroke-width="3" fill="none"/><path d="M20 22 Q20 8 28 4 Q36 8 36 22 Q28 28 20 22Z" stroke="#fff" stroke-width="3" fill="none"/></svg>
    <h3>FLOWERS</h3>
    <p>Lorem ipsum dolor sitconsectetur adipiscing elitsed do eiusmod tempor incididunt utlabore</p>
    <span class="more">READ MORE</span>
  </div>
  <div class="abs bubble b-choc">
    <svg width="70" height="70" viewBox="0 0 70 70"><rect x="18" y="12" width="30" height="46" transform="rotate(40 33 35)" fill="none" stroke="#fff" stroke-width="3"/><path d="M28 28 L42 40 M22 36 L36 48" stroke="#fff" stroke-width="3"/></svg>
    <h3>CHOCOLATE</h3>
    <p>Lorem ipsum dolor sitconsectetur adipiscing elitsed do eiusmod tempor incididunt utlabore</p>
    <span class="more">READ MORE</span>
  </div>
  <div class="abs bubble b-banana">
    <svg width="70" height="70" viewBox="0 0 70 70"><path d="M8 30 Q30 62 62 22 Q50 44 24 36 Z" fill="none" stroke="#fff" stroke-width="3"/><path d="M14 40 Q34 66 62 36" fill="none" stroke="#fff" stroke-width="3"/></svg>
    <h3>BANANAS</h3>
    <p>Lorem ipsum dolor sitconsectetur adipiscing elitsed do eiusmod tempor incididunt utlabore</p>
    <span class="more">READ MORE</span>
  </div>

  <!-- welcome -->
  <h2 class="abs heading welcome-h">WELCOME TO VERANDINA</h2>
  <p class="abs welcome-p">Lorem ipsum dolor sit amet, consectetur adipiscing elit, sed do eiusmod tempor incididunt ut labore et dolore magna aliquauis uspendisse ultrices gravida. Risus commodo viverra maecenas accrem ipsum dolor sit ametconsectetur adipiscingsed do eiusmod tempor incididunt ut labore et dolore magna aliuis ipsum suspendisse ultrices gravidus commodo viverra maecenas accumsan lacus vel facilisisorem ipsum dolor sit amet, consectetur adipiscing ed do eiusmod tempor incididunt ut labore et dolore magna aliqua.</p>

  <div class="abs feature" style="left:193px;top:1189px">
    <div class="ring"><svg width="44" height="34" viewBox="0 0 44 34"><rect x="2" y="4" width="26" height="20" rx="2" fill="var(--blue)"/><path d="M28 10 H38 L42 18 V24 H28Z" fill="var(--blue)"/><circle cx="10" cy="27" r="5" fill="var(--blue)" stroke="#fff" stroke-width="2"/><circle cx="34" cy="27" r="5" fill="var(--blue)" stroke="#fff" stroke-width="2"/></svg></div>
    <span>Duis aute irur</span>
  </div>
  <div class="abs feature" style="left:404px;top:1189px">
    <div class="ring"><svg width="44" height="40" viewBox="0 0 44 40"><path d="M4 6 H20 L40 24 L26 38 L4 18Z" fill="var(--yellow)"/><circle cx="12" cy="13" r="3" fill="#fff"/></svg></div>
    <span>Lorem ipsum dolor</span>
  </div>
  <div class="abs feature" style="left:602px;top:1189px">
    <div class="ring"><svg width="44" height="36" viewBox="0 0 44 36"><path d="M6 32 Q4 6 40 4 Q40 32 10 30Z" fill="var(--green)"/><path d="M6 32 Q18 18 30 12" stroke="#fff" stroke-width="2" fill="none"/></svg></div>
    <span>Iincididunt ut lab</span>
  </div>
  <div class="abs feature" style="left:807px;top:1189px">
    <div class="ring"><svg width="36" height="40" viewBox="0 0 36 40"><path d="M4 4 H32 V20 Q32 32 18 38 Q4 32 4 20Z" fill="#d8232a"/><path d="M12 10 H24 V20 Q24 26 18 30 Q12 26 12 20Z" fill="#fff"/></svg></div>
    <span>Safe Delivery</span>
  </div>

  <!-- flowers row -->
  <svg class="abs photo" style="left:0;top:1438px" viewBox="0 0 600 494" role="img" aria-label="Crates of pink, red and orange cut flowers seen from above"><defs><linearGradient id="fl" x1="0" y1="0" x2="1" y2="1"><stop offset="0" stop-color="#c9475a"/><stop offset=".5" stop-color="#d58cc4"/><stop offset="1" stop-color="#c84a2c"/></linearGradient></defs><rect width="600" height="494" fill="url(#fl)"/></svg>
  <div class="abs panel" style="left:600px;top:1438px"></div>
  <h2 class="abs heading prod-h" style="left:655px;top:1520px">FLOWERS</h2>
  <p class="abs prod-p" style="left:655px;top:1592px">Lorem ipsum dolor sit amet, consectetur adipiscing elsed do eiusmod tempor incididunt ut labore et dolore magna aliquauis ipsuuspendisse ultriceus commodo viverra maecenas accumsan lacus vel facilisis. Lorem ipsum dolor sit amet, consectetur adipiscing elsed do eiusmod tempor incididunt ut labore et dolore magna aliquauis ipsuuspendisse ultriceus commodo viverra maecenas accumsan lacus vel facilisis.</p>
  <div class="abs btn" style="left:655px;top:1791px;background:var(--green)">READ MORE</div>

  <!-- chocolate row -->
  <div class="abs panel" style="left:0;top:1932px"></div>
  <svg class="abs photo" style="left:600px;top:1932px" viewBox="0 0 600 494" role="img" aria-label="Workers in a kitchen preparing trays of chocolates"><defs><linearGradient id="ch" x1="0" y1="0" x2="0" y2="1"><stop offset="0" stop-color="#c9c6bd"/><stop offset=".6" stop-color="#6d5d52"/><stop offset="1" stop-color="#3a2a22"/></linearGradient></defs><rect width="600" height="494" fill="url(#ch)"/></svg>
  <div class="abs notch" style="left:557px;top:1889px"></div>
  <h2 class="abs heading prod-h" style="left:143px;top:2015px">CHOCOLATE</h2>
  <p class="abs prod-p" style="left:143px;top:2087px">Lorem ipsum dolor sit amet, consectetur adipiscing elsed do eiusmod tempor incididunt ut labore et dolore magna aliquauis ipsuuspendisse ultriceus commodo viverra maecenas accumsan lacus vel facilisis. Lorem ipsum dolor sit amet, consectetur adipiscing elsed do eiusmod tempor incididunt ut labore et dolore magna aliquauis ipsuuspendisse ultriceus commodo viverra maecenas accumsan lacus vel facilisis.</p>
  <div class="abs btn" style="left:143px;top:2287px;background:var(--blue)">READ MORE</div>

  <!-- bananas row -->
  <svg class="abs photo" style="left:0;top:2428px" viewBox="0 0 600 494" role="img" aria-label="Green bananas packed in a cardboard box"><defs><linearGradient id="bn" x1="0" y1="0" x2="1" y2="1"><stop offset="0" stop-color="#7fa83a"/><stop offset=".5" stop-color="#a8c13c"/><stop offset="1" stop-color="#b38a5c"/></linearGradient></defs><rect width="600" height="494" fill="url(#bn)"/></svg>
  <div class="abs panel" style="left:600px;top:2428px"></div>
  <div class="abs notch" style="left:557px;top:2385px"></div>
  <h2 class="abs heading prod-h" style="left:655px;top:2511px">BANANAS</h2>
  <p class="abs prod-p" style="left:655px;top:2583px">Lorem ipsum dolor sit amet, consectetur adipiscing elsed do eiusmod tempor incididunt ut labore et dolore magna aliquauis ipsuuspendisse ultriceus commodo viverra maecenas accumsan lacus vel facilisis. Lorem ipsum dolor sit amet, consectetur adipiscing elsed do eiusmod tempor incididunt ut labore et dolore magna aliquauis ipsuuspendisse ultriceus commodo viverra maecenas accumsan lacus vel facilisis.</p>
  <div class="abs btn" style="left:655px;top:2782px;background:var(--yellow)">READ MORE</div>

  <!-- why choose us -->
  <h2 class="abs heading why-h">WHY CHOOSE US</h2>

  <div class="abs why-icon" style="left:143px;top:3151px"><svg width="40" height="40" viewBox="0 0 40 40"><path d="M6 18 H12 V36 H6Z M14 18 L22 4 Q28 6 25 16 H34 Q37 17 36 21 L32 34 Q31 36 28 36 H14Z" fill="none" stroke="#d8232a" stroke-width="3" stroke-linejoin="round"/></svg></div>
  <div class="abs why-t" style="left:257px;top:3152px">QUALITY</div>
  <p class="abs why-p" style="left:257px;top:3193px">Lorem ipsum dolor sit &nbsp;consectetur adipiscing elit, sed do eiusmod tempor incididunt ut labore et dolore magna aliqua.uis ipsum suspendisse ultrices gravidaus commodo viverra</p>

  <div class="abs why-icon" style="left:635px;top:3151px"><svg width="42" height="40" viewBox="0 0 42 40"><polygon points="21,2 26,15 40,15 29,24 33,38 21,30 9,38 13,24 2,15 16,15" fill="var(--green)"/></svg></div>
  <div class="abs why-t" style="left:749px;top:3152px">INDUSTRY EXPERIENCE</div>
  <p class="abs why-p" style="left:749px;top:3193px">Lorem ipsum dolor sit &nbsp;consectetur adipiscing elit, sed do eiusmod tempor incididunt ut labore et dolore magna aliqua.uis ipsum suspendisse ultrices gravidaus commodo viverra</p>

  <div class="abs why-icon" style="left:143px;top:3355px"><svg width="46" height="42" viewBox="0 0 46 42"><circle cx="16" cy="22" r="10" fill="none" stroke="var(--blue)" stroke-width="6" stroke-dasharray="5 3"/><circle cx="34" cy="12" r="6" fill="none" stroke="var(--blue)" stroke-width="4" stroke-dasharray="3 2"/><circle cx="34" cy="32" r="6" fill="none" stroke="var(--blue)" stroke-width="4" stroke-dasharray="3 2"/></svg></div>
  <div class="abs why-t" style="left:257px;top:3360px">FULL SERVICE</div>
  <p class="abs why-p" style="left:257px;top:3401px">Lorem ipsum dolor sit &nbsp;consectetur adipiscing elit, sed do eiusmod tempor incididunt ut labore et dolore magna aliqua.uis ipsum suspendisse ultrices gravidaus commodo viverra</p>

  <div class="abs why-icon" style="left:635px;top:3355px"><svg width="40" height="40" viewBox="0 0 40 40"><circle cx="20" cy="20" r="13" fill="var(--yellow)"/><circle cx="20" cy="20" r="17" fill="none" stroke="var(--yellow)" stroke-width="5" stroke-dasharray="4 3"/></svg></div>
  <div class="abs why-t" style="left:749px;top:3360px">FAIR ORIGIN CERTIFIED</div>
  <p class="abs why-p" style="left:749px;top:3401px">Lorem ipsum dolor sit &nbsp;consectetur adipiscing elit, sed do eiusmod tempor incididunt ut labore et dolore magna aliqua.uis ipsum suspendisse ultrices gravidaus commodo viverra</p>

  <!-- contact -->
  <svg class="abs" style="left:0;top:3570px" width="1200" height="514" viewBox="0 0 1200 514">
    <path d="M0 130 Q600 -40 1200 130 V514 H0Z" fill="var(--dark)"/>
    <path d="M0 130 Q600 -40 1200 130" fill="none" stroke="var(--green)" stroke-width="3"/>
  </svg>
  <h2 class="abs heading contact-h">CONTACT US</h2>
  <div class="abs label" style="left:143px;top:3728px">Get In Touch:</div>
  <div class="abs field" style="left:146px;top:3769px;width:276px;height:29px">NAME :</div>
  <div class="abs field" style="left:433px;top:3769px;width:276px;height:29px">PHONE :</div>
  <div class="abs field" style="left:146px;top:3810px;width:563px;height:29px">EMAIL :</div>
  <div class="abs field" style="left:146px;top:3851px;width:563px;height:64px">MESSAGE :</div>
  <div class="abs submit">SUBMIT</div>

  <div class="abs label" style="left:783px;top:3728px">Contact Information</div>
  <div class="abs info-icon" style="left:782px;top:3770px"><svg width="14" height="18" viewBox="0 0 14 18"><path d="M7 17 Q1 9 1 6 A6 6 0 0 1 13 6 Q13 9 7 17Z" fill="none" stroke="#fff" stroke-width="1.6"/><circle cx="7" cy="6" r="2" fill="#fff"/></svg></div>
  <div class="abs info-t" style="left:832px;top:3768px">122Lorem ipsum dolor sit amet,consec tetur adipiscing elit</div>
  <div class="abs info-icon" style="left:782px;top:3820px"><svg width="16" height="16" viewBox="0 0 16 16"><path d="M3 1 L6 1 L7 5 L5 6 Q6 9 10 11 L11 9 L15 10 L15 13 Q14 15 12 15 Q2 13 1 3 Q1 1 3 1Z" fill="none" stroke="#fff" stroke-width="1.4"/></svg></div>
  <div class="abs info-t" style="left:832px;top:3828px">Phone : 1 555 010 2040</div>
  <div class="abs info-icon" style="left:782px;top:3871px"><svg width="16" height="12" viewBox="0 0 16 12"><rect x="0" y="0" width="16" height="12" rx="1" fill="#fff"/><path d="M0 1 L8 7 L16 1" stroke="var(--dark)" stroke-width="1.4" fill="none"/></svg></div>
  <div class="abs info-t" style="left:832px;top:3878px">Email : info@verandina.com</div>

  <div class="abs social" style="left:786px;top:3927px;background:var(--blue)"></div>
  <div class="abs social" style="left:818px;top:3927px;background:#1da1f2"></div>
  <div class="abs social" style="left:849px;top:3927px;background:#e02a20"></div>
  <div class="abs social" style="left:881px;top:3927px;background:#b08a5a"></div>

  <div class="abs rule"></div>
  <div class="abs copy">Copyrights © 2020, Verandina. All Rights Reserved. &nbsp;| &nbsp;Privacy Policy &nbsp;| &nbsp;Resources</div>
</div>
</body>
</html>
```